Business Card Design

Looking for business card designs for a new business. there will be two cards of the same design (both lots of information below in contact info). We would like the logo diagonally across the card with the information split above and below the logo similar to sketch. happy to look at similar alternatives
Please use same colours as in logo design

Industry/Entity Type

Business

Contact Information for Business Card

Dwight Halloran
mob - 0491 738 204
ph - 02 6148 3920
fax - 02 6148 3975
email - dwight@kestrelbeams.com.au
14 Larkmoor Road, Brenmore NSW 2395

Colin Marchetti
mob - 0438 912 557
ph - 02 6148 3920
fax - 02 6148 3975
email - colin@kestrelbeams.com.au

```html
<!DOCTYPE html>
<html lang="en">
<head>
<meta charset="utf-8">
<title>Kestrel Beams – Business Cards</title>
<link rel="stylesheet" href="https://fonts.googleapis.com/css2?family=Source+Sans+3:wght@400;600;700&display=swap">
<style>
  :root {
    --teal: #13857a;
    --ink: #111111;
    --card: #ffffff;
    --backdrop: #e9e7e3;
    --text: #222222;
    --light: #ffffff;
    --edge: #3a3a3a;
  }
  * { box-sizing: border-box; margin: 0; padding: 0; }
  html, body {
    width: 1146px;
    height: 1200px;
    overflow: hidden;
  }
  body {
    position: relative;
    background: var(--backdrop);
    font-family: "Source Sans 3", sans-serif;
    color: var(--text);
  }
  .card {
    position: absolute;
    width: 944px;
    height: 537px;
    background: var(--card);
    border: 1px solid var(--edge);
    overflow: hidden;
  }
  .card--front { left: 171px; top: 50px; }
  .card--back  { left: 29px;  top: 633px; }

  .brand {
    position: absolute;
    display: flex;
    align-items: center;
    gap: 16px;
  }
  .brand__mark {
    width: 50px;
    height: 50px;
    background: var(--teal);
  }
  .brand__name {
    font-weight: 700;
    font-size: 80px;
    line-height: 1;
    color: var(--ink);
    letter-spacing: -1px;
  }
  .card--front .brand { left: 96px; top: 78px; }
  .card--back .brand { left: 0; right: 0; top: 210px; justify-content: center; }

  .holder {
    position: absolute;
    left: 93px;
    top: 284px;
    font-weight: 700;
    font-size: 29px;
    color: var(--teal);
  }
  .address {
    position: absolute;
    left: 93px;
    top: 362px;
    font-style: normal;
    font-size: 23px;
    line-height: 37px;
    color: var(--text);
  }
  .base-band {
    position: absolute;
    left: 0;
    top: 0;
    width: 944px;
    height: 537px;
  }
  .contacts {
    position: absolute;
    right: 24px;
    top: 364px;
    list-style: none;
    text-align: right;
    color: var(--light);
    font-size: 22px;
    line-height: 36px;
  }
  .contacts li {
    display: flex;
    justify-content: flex-end;
    align-items: center;
    gap: 6px;
  }
  .contacts svg { width: 18px; height: 18px; fill: var(--light); }

  .website {
    position: absolute;
    left: 0;
    right: 0;
    top: 426px;
    text-align: center;
    font-size: 30px;
    letter-spacing: 2px;
    color: var(--text);
  }
  .website strong { font-weight: 700; }
</style>
</head>
<body>

  <section class="card card--front" aria-label="Business card front">
    <div class="brand">
      <span class="brand__mark"></span>
      <span class="brand__name">Kestrel Beams</span>
    </div>

    <svg class="base-band" viewBox="0 0 944 537" role="img" aria-label="Decorative base band in teal and black">
      <defs>
        <linearGradient id="bandTone" x1="0" y1="0" x2="1" y2="0">
          <stop offset="0" stop-color="var(--teal)"/>
          <stop offset="0.55" stop-color="var(--ink)"/>
        </linearGradient>
      </defs>
      <path fill="url(#bandTone)" d="M0,470 C300,520 600,390 944,236 L944,537 L0,537 Z"/>
    </svg>

    <h1 class="holder">Colin Marchetti</h1>
    <address class="address">14 Larkmoor Road<br>Brenmore NSW 2395</address>

    <ul class="contacts">
      <li>
        <svg viewBox="0 0 24 24" aria-label="Phone"><path d="M6.6 10.8a15.1 15.1 0 0 0 6.6 6.6l2.2-2.2a1 1 0 0 1 1-.25 11.4 11.4 0 0 0 3.6.57 1 1 0 0 1 1 1V20a1 1 0 0 1-1 1A17 17 0 0 1 3 4a1 1 0 0 1 1-1h3.5a1 1 0 0 1 1 1c0 1.25.2 2.45.57 3.6a1 1 0 0 1-.25 1z"/></svg>
        02 6148 3920
      </li>
      <li>
        <svg viewBox="0 0 24 24" aria-label="Mobile"><path d="M7 1h10a2 2 0 0 1 2 2v18a2 2 0 0 1-2 2H7a2 2 0 0 1-2-2V3a2 2 0 0 1 2-2zm0 3v13h10V4zm5 15a1.2 1.2 0 1 0 0 2.4A1.2 1.2 0 0 0 12 19z"/></svg>
        0438 912 557
      </li>
      <li>
        <svg viewBox="0 0 24 24" aria-label="Fax"><path d="M7 3h10v5H7zM4 9h16a2 2 0 0 1 2 2v6h-4v4H6v-4H2v-6a2 2 0 0 1 2-2zm4 7v3h8v-3z"/></svg>
        02 6148 3975
      </li>
      <li>
        <svg viewBox="0 0 24 24" aria-label="Email"><path d="M2 6l10 6 10-6v12H2zM2 4h20l-10 6z"/></svg>
        colin@kestrelbeams.com.au
      </li>
    </ul>
  </section>

  <section class="card card--back" aria-label="Business card back">
    <div class="brand">
      <span class="brand__mark"></span>
      <span class="brand__name">Kestrel Beams</span>
    </div>
    <p class="website">www.<strong>kestrelbeams</strong>.com.au</p>
  </section>

</body>
</html>
```